Online Dating Website called WinkAtWheel.com

PLEASE CAN ALL PARTICIPATING DESIGNERS PLEASE SUBMIT ALL PAGES AS DETAILED IN THE ORIGINAL BRIEF BELOW WITHIN 48 HOURS TO AVOID WINKATWHEEL EXTENDING THE CONTEST FURTHER.

We have an online dating website that is 95% fully functional and now require an exciting and creative designer to help us create the best dating experience. We are looking for your ideas on a couple of our key pages. These are our landing, profile and search page. We already have a homepage that we are happy with and winning designers will look to build upon the foundations of the homepage and extend them through their designs.

The premise of the site is the idea that if you've ever seen someone out driving and wished you could communicate because you found them attractive, how would you? Well with WinkAtWheel.com you can. Just enter their vehicle registration number (license plate) in to the website in order to get in touch, flirt and develop a relationship. It also allows users to find each other based on other criteria. It acts as both a specialist service and a normal dating website.

The pages that require developing are 1) our landing page, this is the page users see when they first login to the site, it comprises various pieces of information but it's primary function is a live feed of events generated based on the users favourited profiles and interactions with the user. 2) The profile page is the page where users can edit their own information, given the nature of this page we are looking for a creative design that gives this page some flair. 3) Finally we are looking for ideas for our search page, this page needs to provide a list of users who meet the user's search requirements and display the profile of a selected user.
Updates

Project Deadline Extended
Reason: We've asked for certain pages in our brief to be designed and this still hasn't been done. We've contacted the designers that have currently submitted designs and requested this several times. We still await for this to happen.

Target Market(s)

Male or Female age 18+

Industry/Entity Type

Dating

Requirements
Must have
• Our must have feature is a designer with an open mind. The functionality of the site must be present, all we ask is for you to be creative with the layout. Think out side of the box, change the colours, the layout, and the background as you feel. Make it look current and appealing to the user.
Nice to have
• Theme's carried through from the home page
Should not have
• Do not include Comic Sans or Times New Roman font in your designs.

```html
<!DOCTYPE html>
<html lang="en">
<head>
<meta charset="utf-8">
<title>WinkAtWheel – Feed</title>
<link href="https://fonts.googleapis.com/css2?family=Open+Sans:wght@400;600;700&display=swap" rel="stylesheet">
<style>
:root{
  --bar:#1c1c22;
  --pink:#e8348c;
  --green:#35a83a;
  --blue:#1f6fc0;
  --purple:#7a4fc0;
  --text:#333;
  --muted:#666;
  --line:#e4e4e4;
  --card:#ffffff;
  --tick:#3aa53f;
}
*{box-sizing:border-box;margin:0;padding:0}
html,body{width:690px;height:1200px;overflow:hidden}
body{font-family:"Open Sans",Arial,sans-serif;color:var(--text);position:relative;font-size:7px}
.backdrop{position:absolute;inset:0;background:
  radial-gradient(circle at 20% 20%,#c0307a 0,transparent 30%),
  radial-gradient(circle at 80% 40%,#2b3fa8 0,transparent 35%),
  radial-gradient(circle at 50% 70%,#8a2a6a 0,transparent 35%),
  radial-gradient(circle at 30% 90%,#3a2a80 0,transparent 30%),
  linear-gradient(180deg,#2a1040,#4a1a50 40%,#1d1230)}
.topbar{position:absolute;left:0;top:0;width:690px;height:32px;background:var(--bar);display:flex;align-items:center;padding:0 10px;color:#fff}
.brand{font-size:16px;font-weight:600;display:flex;align-items:center;gap:4px}
.brand .dot{width:10px;height:10px;background:var(--pink);border-radius:50%}
.nav{display:flex;gap:20px;margin-left:22px;font-size:7.5px;font-weight:600}
.account{margin-left:auto;display:flex;gap:14px;font-size:7.5px;font-weight:600}
.col{position:absolute;top:44px}
.left{left:10px;width:136px}
.center{left:156px;width:377px}
.right{left:544px;width:135px}
.panel{background:var(--card);border-radius:3px;margin-bottom:12px;overflow:hidden}
.panel-head{height:25px;color:#fff;font-weight:700;font-size:11px;display:flex;align-items:center;justify-content:space-between;padding:0 8px;white-space:nowrap}
.panel-head .badge{width:15px;height:15px;border-radius:50%;background:rgba(255,255,255,.3)}
.h-green{background:var(--green)}.h-blue{background:var(--blue)}.h-pink{background:var(--pink)}.h-purple{background:var(--purple)}
.profile-body{padding:6px 8px 8px}
.profile-body .age{font-weight:700;font-size:7px;margin-bottom:6px}
.car{height:74px;width:114px;background:linear-gradient(135deg,#c8d4dc,#b21f24 50%,#6d1a1e);margin-bottom:10px}
.row{display:flex;gap:4px;margin-bottom:6px}
.input{flex:1;height:17px;border:1px solid #ccc;border-radius:2px;font-size:6.5px;color:#888;display:flex;align-items:center;padding:0 4px}
.btn{height:17px;border-radius:2px;color:#fff;font-weight:700;font-size:6.5px;display:flex;align-items:center;justify-content:center;padding:0 5px}
.btn.green{background:var(--green)}.btn.pink{background:var(--pink)}.btn.blue{background:var(--blue)}
.half{flex:1}
.search-body{padding:8px}
.big-search{width:40px;height:42px;border-radius:3px;background:var(--purple);color:#fff;font-weight:700;font-size:6.5px;display:flex;align-items:flex-end;justify-content:center;padding-bottom:4px}
.stat-title{background:#eee;font-weight:700;font-size:7.5px;height:24px;display:flex;align-items:center;padding:0 8px}
.stat-row{display:flex;justify-content:space-between;align-items:center;height:13px;padding:0 8px;font-size:6.5px;color:var(--muted)}
.stat-row.gap{margin-bottom:5px}
.stat-row b{color:var(--blue);font-weight:600}
.tick{color:var(--tick);font-weight:700}
.fav-item{display:flex;gap:10px;padding:10px 8px;border-bottom:1px solid var(--line)}
.fav-photo{width:34px;height:34px;background:linear-gradient(135deg,#d9cdbd,#8aa0a8)}
.fav-item b{display:block;font-size:7px}
.fav-item span{display:block;color:var(--muted);font-size:6.3px;line-height:1.4}
.feed-card{background:var(--card);border-radius:3px;height:102px;margin-bottom:12px;padding:8px 10px;box-shadow:0 2px 4px rgba(0,0,0,.3)}
.feed-title{color:var(--pink);font-size:10px;font-weight:600;padding-bottom:5px;border-bottom:1px solid var(--line);margin-bottom:8px}
.feed-body{display:flex;gap:12px}
.feed-thumb{width:52px;height:52px;flex:none;background:radial-gradient(circle,#a3202f,#1a0a0c 70%)}
.feed-text{width:238px;color:var(--muted);font-size:6.8px;line-height:10.7px}
.feed-meta{border-left:1px solid var(--line);padding-left:6px;font-size:6.5px;color:var(--muted);display:flex;flex-direction:column;gap:9px}
.feed-meta div{display:flex;align-items:center;gap:5px}
.welcome{height:184px;background:linear-gradient(180deg,#f8e8f0,#fff);text-align:center;padding-top:10px}
.welcome .hearts{height:80px;display:flex;justify-content:center;align-items:center}
.welcome .word{background:var(--pink);color:#fff;font-weight:700;font-size:17px;padding:7px 12px;border-radius:22px}
.welcome p{font-size:13px;line-height:1.3;font-weight:600;color:#222;margin-top:12px}
.welcome .big{font-size:15px}
.welcome .hl-pink{color:var(--pink);font-size:17px;font-weight:700}
.welcome .hl-blue{color:var(--blue);font-weight:700}
.match-list{padding:4px 6px}
.match-row{font-size:6.5px;color:var(--muted);padding:2px 0;display:flex;gap:3px;line-height:1.35}
.match-row i{flex:none;width:7px;height:6px;background:var(--blue);border-radius:1px;margin-top:1px}
.match-row b{color:#222}
.match-grid{display:grid;grid-template-columns:1fr 1fr;gap:8px 12px;padding:6px 8px 8px}
.match-tile{border:3px solid var(--blue);border-radius:3px;background:var(--blue)}
.match-tile .pic{height:52px;background:linear-gradient(135deg,#d8d0c2,#8ea7b0)}
.match-tile span{display:block;color:#fff;font-weight:700;font-size:7px;text-align:center;padding:2px 0}
.h-small{font-size:10.5px;padding:0 6px}
.bg-grid{display:grid;grid-template-columns:repeat(3,1fr);gap:6px;padding:8px}
.bg-grid div{height:36px;border-radius:2px}
.chat{position:absolute;right:0;bottom:0;width:88px;height:18px;background:#fff;color:#111;font-weight:700;font-size:7px;display:flex;align-items:center;justify-content:center;gap:4px;border-radius:3px 0 0 0}
</style>
</head>
<body>
<div class="backdrop" role="img" aria-label="Blurred nightlife crowd with colourful lights"></div>

<header class="topbar">
  <div class="brand">winkatwheel <span class="dot"></span></div>
  <nav class="nav"><span>Home</span><span>Profile</span><span>Message</span><span>Matches</span><span>Search</span></nav>
  <div class="account"><span>Support</span><span>My Account</span></div>
</header>

<aside class="col left">
  <section class="panel">
    <div class="panel-head h-green">LEE</div>
    <div class="profile-body">
      <div class="age">(24 years old - castleford)</div>
      <div class="car" role="img" aria-label="Red classic convertible car"></div>
      <div class="row"><div class="input">How are you?</div><div class="btn green">UPDATE</div></div>
      <div class="row"><div class="btn pink half">PROFILE</div><div class="btn blue half">UPLOAD</div></div>
    </div>
  </section>

  <section class="panel">
    <div class="panel-head h-purple">SEEN SOMEONE? <span class="badge"></span></div>
    <div class="search-body">
      <div class="row"><div class="input">Search REG</div><div class="btn pink">SEARCH</div></div>
      <div class="row">
        <div style="flex:1;display:flex;flex-direction:column;gap:6px">
          <div class="input">Make</div><div class="input">Colour</div>
        </div>
        <div class="big-search">SEARCH</div>
      </div>
    </div>
  </section>

  <section class="panel">
    <div class="panel-head h-blue">YOUR STATS <span class="badge"></span></div>
    <div class="stat-title">LIKES &nbsp;124</div>
    <div class="stat-row">Images you have liked<b>32</b></div>
    <div class="stat-row">Statuses you have liked<b>67</b></div>
    <div class="stat-row">Likes on your images<b>20</b></div>
    <div class="stat-row gap">Likes on your Statuses<b>55</b></div>
    <div class="stat-title">MESSAGES &nbsp;171</div>
    <div class="stat-row">Sent Messages<b>66</b></div>
    <div class="stat-row gap">Received Messages<b>105</b></div>
    <div class="stat-title">FAVOURITES &nbsp;20</div>
    <div class="stat-row">Your Favourites<b>12</b></div>
    <div class="stat-row gap">Favourited by<b>8</b></div>
  </section>

  <section class="panel">
    <div class="panel-head h-pink">FEED FILTER <span class="badge"></span></div>
    <div class="stat-title">STATUS UPDATES</div>
    <div class="stat-row">Statuses by others<span class="tick">✓</span></div>
    <div class="stat-row">Statuses by me<span class="tick">✓</span></div>
    <div class="stat-title">IMAGE UPLOADS</div>
    <div class="stat-row">Uploads by others<span class="tick">✓</span></div>
    <div class="stat-row">Uploads by me<span class="tick">✓</span></div>
    <div class="stat-title">PROFILE UPDATES</div>
    <div class="stat-row">Updates by others<span class="tick">✓</span></div>
    <div class="stat-row">Updates by me<span class="tick">✓</span></div>
    <div class="stat-row">Images Changes by others<span class="tick">✓</span></div>
    <div class="stat-row">Images Changes by me<span class="tick">✓</span></div>
    <div class="stat-title">OTHERS</div>
    <div class="stat-row">Received Messages<span class="tick">✓</span></div>
    <div class="stat-row">Views<span class="tick">✓</span></div>
    <div class="stat-row gap">Favouriting<span class="tick">✓</span></div>
  </section>

  <section class="panel">
    <div class="panel-head h-green">YOUR FAVOURITES <span class="badge"></span></div>
    <div class="search-body" style="padding-bottom:0"><div class="row"><div class="input">Type a name :</div><div class="btn green">SEARCH</div></div></div>
    <div class="fav-item"><div class="fav-photo" role="img" aria-label="Couple portrait"></div><div><b>JENNY</b><span>22 years old</span><span>Leeds</span></div></div>
    <div class="fav-item"><div class="fav-photo" role="img" aria-label="Couple portrait"></div><div><b>JENNY</b><span>22 years old</span><span>Leeds</span></div></div>
    <div class="fav-item"><div class="fav-photo" role="img" aria-label="Couple portrait"></div><div><b>JENNY</b><span>22 years old</span><span>Leeds</span></div></div>
    <div class="fav-item" style="border:0"><div class="fav-photo" role="img" aria-label="Couple portrait"></div><div><b>JENNY</b><span>22 years old</span><span>Leeds</span></div></div>
  </section>
</aside>

<main class="col center">
  <article class="feed-card"><h3 class="feed-title">Lady Changed her Status</h3><div class="feed-body"><div class="feed-thumb" role="img" aria-label="Red heart artwork"></div><p class="feed-text">This is Lumapaint's version of Lorem Ipsum. Proin gravida nibh vel velit auctor aliquet. Aenean sollicitudin, lorem quis bibendum auctor, nisi elit consequat ipsum, nec sagittis sem nibh id elit. Duis sed odio sit amet nibh vulputate cursus a sit amet mauris.</p><div class="feed-meta"><div><svg width="8" height="8"><rect x="0.5" y="1.5" width="7" height="6" fill="none" stroke="#e8348c"/><rect x="0.5" y="1.5" width="7" height="2" fill="#e8348c"/></svg>Tuesday</div><div><svg width="8" height="8"><circle cx="4" cy="4" r="3.3" fill="none" stroke="#e8348c"/><path d="M4 2v2h2" stroke="#e8348c" fill="none"/></svg>22 : 56</div><div><svg width="8" height="8"><path d="M4 7L1 4a1.6 1.6 0 0 1 3-2a1.6 1.6 0 0 1 3 2z" fill="#e8348c"/></svg>Like</div></div></div></article>
  <article class="feed-card"><h3 class="feed-title">Lady Changed her Status</h3><div class="feed-body"><div class="feed-thumb" role="img" aria-label="Red heart artwork"></div><p class="feed-text">This is Lumapaint's version of Lorem Ipsum. Proin gravida nibh vel velit auctor aliquet. Aenean sollicitudin, lorem quis bibendum auctor, nisi elit consequat ipsum, nec sagittis sem nibh id elit. Duis sed odio sit amet nibh vulputate cursus a sit amet mauris.</p><div class="feed-meta"><div><svg width="8" height="8"><rect x="0.5" y="1.5" width="7" height="6" fill="none" stroke="#e8348c"/><rect x="0.5" y="1.5" width="7" height="2" fill="#e8348c"/></svg>Tuesday</div><div><svg width="8" height="8"><circle cx="4" cy="4" r="3.3" fill="none" stroke="#e8348c"/><path d="M4 2v2h2" stroke="#e8348c" fill="none"/></svg>22 : 56</div><div><svg width="8" height="8"><path d="M4 7L1 4a1.6 1.6 0 0 1 3-2a1.6 1.6 0 0 1 3 2z" fill="#e8348c"/></svg>Like</div></div></div></article>
  <article class="feed-card"><h3 class="feed-title">Lady Changed her Status</h3><div class="feed-body"><div class="feed-thumb" role="img" aria-label="Red heart artwork"></div><p class="feed-text">This is Lumapaint's version of Lorem Ipsum. Proin gravida nibh vel velit auctor aliquet. Aenean sollicitudin, lorem quis bibendum auctor, nisi elit consequat ipsum, nec sagittis sem nibh id elit. Duis sed odio sit amet nibh vulputate cursus a sit amet mauris.</p><div class="feed-meta"><div><svg width="8" height="8"><rect x="0.5" y="1.5" width="7" height="6" fill="none" stroke="#e8348c"/><rect x="0.5" y="1.5" width="7" height="2" fill="#e8348c"/></svg>Tuesday</div><div><svg width="8" height="8"><circle cx="4" cy="4" r="3.3" fill="none" stroke="#e8348c"/><path d="M4 2v2h2" stroke="#e8348c" fill="none"/></svg>22 : 56</div><div><svg width="8" height="8"><path d="M4 7L1 4a1.6 1.6 0 0 1 3-2a1.6 1.6 0 0 1 3 2z" fill="#e8348c"/></svg>Like</div></div></div></article>
  <article class="feed-card"><h3 class="feed-title">Lady Changed her Status</h3><div class="feed-body"><div class="feed-thumb" role="img" aria-label="Red heart artwork"></div><p class="feed-text">This is Lumapaint's version of Lorem Ipsum. Proin gravida nibh vel velit auctor aliquet. Aenean sollicitudin, lorem quis bibendum auctor, nisi elit consequat ipsum, nec sagittis sem nibh id elit. Duis sed odio sit amet nibh vulputate cursus a sit amet mauris.</p><div class="feed-meta"><div><svg width="8" height="8"><rect x="0.5" y="1.5" width="7" height="6" fill="none" stroke="#e8348c"/><rect x="0.5" y="1.5" width="7" height="2" fill="#e8348c"/></svg>Tuesday</div><div><svg width="8" height="8"><circle cx="4" cy="4" r="3.3" fill="none" stroke="#e8348c"/><path d="M4 2v2h2" stroke="#e8348c" fill="none"/></svg>22 : 56</div><div><svg width="8" height="8"><path d="M4 7L1 4a1.6 1.6 0 0 1 3-2a1.6 1.6 0 0 1 3 2z" fill="#e8348c"/></svg>Like</div></div></div></article>
  <article class="feed-card"><h3 class="feed-title">Lady Changed her Status</h3><div class="feed-body"><div class="feed-thumb" role="img" aria-label="Red heart artwork"></div><p class="feed-text">This is Lumapaint's version of Lorem Ipsum. Proin gravida nibh vel velit auctor aliquet. Aenean sollicitudin, lorem quis bibendum auctor, nisi elit consequat ipsum, nec sagittis sem nibh id elit. Duis sed odio sit amet nibh vulputate cursus a sit amet mauris.</p><div class="feed-meta"><div><svg width="8" height="8"><rect x="0.5" y="1.5" width="7" height="6" fill="none" stroke="#e8348c"/><rect x="0.5" y="1.5" width="7" height="2" fill="#e8348c"/></svg>Tuesday</div><div><svg width="8" height="8"><circle cx="4" cy="4" r="3.3" fill="none" stroke="#e8348c"/><path d="M4 2v2h2" stroke="#e8348c" fill="none"/></svg>22 : 56</div><div><svg width="8" height="8"><path d="M4 7L1 4a1.6 1.6 0 0 1 3-2a1.6 1.6 0 0 1 3 2z" fill="#e8348c"/></svg>Like</div></div></div></article>
  <article class="feed-card"><h3 class="feed-title">Lady Changed her Status</h3><div class="feed-body"><div class="feed-thumb" role="img" aria-label="Red heart artwork"></div><p class="feed-text">This is Lumapaint's version of Lorem Ipsum. Proin gravida nibh vel velit auctor aliquet. Aenean sollicitudin, lorem quis bibendum auctor, nisi elit consequat ipsum, nec sagittis sem nibh id elit. Duis sed odio sit amet nibh vulputate cursus a sit amet mauris.</p><div class="feed-meta"><div><svg width="8" height="8"><rect x="0.5" y="1.5" width="7" height="6" fill="none" stroke="#e8348c"/><rect x="0.5" y="1.5" width="7" height="2" fill="#e8348c"/></svg>Tuesday</div><div><svg width="8" height="8"><circle cx="4" cy="4" r="3.3" fill="none" stroke="#e8348c"/><path d="M4 2v2h2" stroke="#e8348c" fill="none"/></svg>22 : 56</div><div><svg width="8" height="8"><path d="M4 7L1 4a1.6 1.6 0 0 1 3-2a1.6 1.6 0 0 1 3 2z" fill="#e8348c"/></svg>Like</div></div></div></article>
  <article class="feed-card"><h3 class="feed-title">Lady Changed her Status</h3><div class="feed-body"><div class="feed-thumb" role="img" aria-label="Red heart artwork"></div><p class="feed-text">This is Lumapaint's version of Lorem Ipsum. Proin gravida nibh vel velit auctor aliquet. Aenean sollicitudin, lorem quis bibendum auctor, nisi elit consequat ipsum, nec sagittis sem nibh id elit. Duis sed odio sit amet nibh vulputate cursus a sit amet mauris.</p><div class="feed-meta"><div><svg width="8" height="8"><rect x="0.5" y="1.5" width="7" height="6" fill="none" stroke="#e8348c"/><rect x="0.5" y="1.5" width="7" height="2" fill="#e8348c"/></svg>Tuesday</div><div><svg width="8" height="8"><circle cx="4" cy="4" r="3.3" fill="none" stroke="#e8348c"/><path d="M4 2v2h2" stroke="#e8348c" fill="none"/></svg>22 : 56</div><div><svg width="8" height="8"><path d="M4 7L1 4a1.6 1.6 0 0 1 3-2a1.6 1.6 0 0 1 3 2z" fill="#e8348c"/></svg>Like</div></div></div></article>
  <article class="feed-card"><h3 class="feed-title">Lady Changed her Status</h3><div class="feed-body"><div class="feed-thumb" role="img" aria-label="Red heart artwork"></div><p class="feed-text">This is Lumapaint's version of Lorem Ipsum. Proin gravida nibh vel velit auctor aliquet. Aenean sollicitudin, lorem quis bibendum auctor, nisi elit consequat ipsum, nec sagittis sem nibh id elit. Duis sed odio sit amet nibh vulputate cursus a sit amet mauris.</p><div class="feed-meta"><div><svg width="8" height="8"><rect x="0.5" y="1.5" width="7" height="6" fill="none" stroke="#e8348c"/><rect x="0.5" y="1.5" width="7" height="2" fill="#e8348c"/></svg>Tuesday</div><div><svg width="8" height="8"><circle cx="4" cy="4" r="3.3" fill="none" stroke="#e8348c"/><path d="M4 2v2h2" stroke="#e8348c" fill="none"/></svg>22 : 56</div><div><svg width="8" height="8"><path d="M4 7L1 4a1.6 1.6 0 0 1 3-2a1.6 1.6 0 0 1 3 2z" fill="#e8348c"/></svg>Like</div></div></div></article>
  <article class="feed-card"><h3 class="feed-title">Lady Changed her Status</h3><div class="feed-body"><div class="feed-thumb" role="img" aria-label="Red heart artwork"></div><p class="feed-text">This is Lumapaint's version of Lorem Ipsum. Proin gravida nibh vel velit auctor aliquet. Aenean sollicitudin, lorem quis bibendum auctor, nisi elit consequat ipsum, nec sagittis sem nibh id elit. Duis sed odio sit amet nibh vulputate cursus a sit amet mauris.</p><div class="feed-meta"><div><svg width="8" height="8"><rect x="0.5" y="1.5" width="7" height="6" fill="none" stroke="#e8348c"/><rect x="0.5" y="1.5" width="7" height="2" fill="#e8348c"/></svg>Tuesday</div><div><svg width="8" height="8"><circle cx="4" cy="4" r="3.3" fill="none" stroke="#e8348c"/><path d="M4 2v2h2" stroke="#e8348c" fill="none"/></svg>22 : 56</div><div><svg width="8" height="8"><path d="M4 7L1 4a1.6 1.6 0 0 1 3-2a1.6 1.6 0 0 1 3 2z" fill="#e8348c"/></svg>Like</div></div></div></article>
  <article class="feed-card"><h3 class="feed-title">Lady Changed her Status</h3><div class="feed-body"><div class="feed-thumb" role="img" aria-label="Red heart artwork"></div><p class="feed-text">This is Lumapaint's version of Lorem Ipsum. Proin gravida nibh vel velit auctor aliquet. Aenean sollicitudin, lorem quis bibendum auctor, nisi elit consequat ipsum, nec sagittis sem nibh id elit. Duis sed odio sit amet nibh vulputate cursus a sit amet mauris.</p><div class="feed-meta"><div><svg width="8" height="8"><rect x="0.5" y="1.5" width="7" height="6" fill="none" stroke="#e8348c"/><rect x="0.5" y="1.5" width="7" height="2" fill="#e8348c"/></svg>Tuesday</div><div><svg width="8" height="8"><circle cx="4" cy="4" r="3.3" fill="none" stroke="#e8348c"/><path d="M4 2v2h2" stroke="#e8348c" fill="none"/></svg>22 : 56</div><div><svg width="8" height="8"><path d="M4 7L1 4a1.6 1.6 0 0 1 3-2a1.6 1.6 0 0 1 3 2z" fill="#e8348c"/></svg>Like</div></div></div></article>
</main>

<aside class="col right">
  <section class="panel welcome">
    <div class="hearts"><span class="word">WELCOME</span></div>
    <p>OUR SITE IS<br><span class="hl-pink">CURRENTLY</span><br><span class="big">FREE DURING</span><br><span class="big"><span class="hl-blue">BETA</span> TESTING</span></p>
  </section>

  <section class="panel">
    <div class="panel-head h-blue">YOUR MATCHES <span class="badge"></span></div>
    <div class="match-list">
      <div class="match-row"><i></i><span><b>WAW</b> has uploaded a new image</span></div>
      <div class="match-row"><i></i><span><b>WAW</b> has uploaded a new image</span></div>
      <div class="match-row"><i></i><span><b>Lee</b> has uploaded a new image</span></div>
      <div class="match-row"><i></i><span><b>WAW</b> has updated his status</span></div>
      <div class="match-row"><i></i><span><b>WAW</b> has updated his status</span></div>
      <div class="match-row"><i></i><span><b>WAW</b> has updated his status</span></div>
      <div class="match-row"><i></i><span><b>Lee</b> has updated his status</span></div>
      <div class="match-row"><i></i><span><b>Eduadoxyz</b> has uploaded a new image</span></div>
      <div class="match-row"><i></i><span><b>Rangi</b> has uploaded a new image</span></div>
      <div class="match-row"><i></i><span><b>Lady</b> has updated her status</span></div>
    </div>
    <div class="match-grid">
      <div class="match-tile"><div class="pic" role="img" aria-label="Couple portrait"></div><span>WAW</span></div>
      <div class="match-tile"><div class="pic" role="img" aria-label="Couple portrait"></div><span>Jack</span></div>
      <div class="match-tile"><div class="pic" role="img" aria-label="Couple portrait"></div><span>Example</span></div>
      <div class="match-tile"><div class="pic" role="img" aria-label="Couple portrait"></div><span>Work</span></div>
      <div class="match-tile"><div class="pic" role="img" aria-label="Couple portrait"></div><span>Johnny</span></div>
      <div class="match-tile"><div class="pic" role="img" aria-label="Couple portrait"></div><span>Playbook</span></div>
      <div class="match-tile"><div class="pic" role="img" aria-label="Couple portrait"></div><span>Boby</span></div>
      <div class="match-tile"><div class="pic" role="img" aria-label="Couple portrait"></div><span>WAW</span></div>
    </div>
  </section>

  <section class="panel">
    <div class="panel-head h-pink h-small">BACKGROUND SELECT</div>
    <div class="bg-grid" role="img" aria-label="Background theme thumbnails">
      <div style="background:linear-gradient(135deg,#c88060,#5a3a40)"></div>
      <div style="background:linear-gradient(135deg,#9fd8d0,#3a6a70)"></div>
      <div style="background:linear-gradient(135deg,#f07aa0,#d63a70)"></div>
      <div style="background:linear-gradient(135deg,#c88060,#5a3a40)"></div>
      <div style="background:linear-gradient(135deg,#a8d870,#4a7040)"></div>
      <div style="background:linear-gradient(135deg,#f07aa0,#d63a70)"></div>
      <div style="background:linear-gradient(135deg,#3a3430,#151210)"></div>
      <div style="background:linear-gradient(135deg,#6ab0b8,#1f4a60)"></div>
      <div style="background:linear-gradient(135deg,#e0a070,#8a4a30)"></div>
      <div style="background:linear-gradient(135deg,#3a3430,#151210)"></div>
      <div style="background:linear-gradient(135deg,#6ab0b8,#1f4a60)"></div>
      <div style="background:linear-gradient(135deg,#e0a070,#8a4a30)"></div>
    </div>
  </section>
</aside>

<div class="chat"><svg width="9" height="8"><path d="M1 1h7v5H4L2 7.5V6H1z" fill="#111"/></svg>OPEN CHAT</div>
</body>
</html>
```